Photographer's price list

I am a photographer who runs a studio (Marrowfield Studio) and need to have a document to send clients detailing my packages (collections) and prices. I have written the text in a word document and need a designer to lay it out for me using my logo and two specific fonts: DejaVu Sans and LainieDaySH.

The look should be clean and modern and keep in the same style as my logo. I will primarily be using the final product as a PDF file to email to potential clients. It should stay black and white.

I would also like to be able to update the text myself as my prices and packages change. So I would like a PSD file.

I think I would like for the document to be in landscape format with "Collections" on one side and A la Carte on the other, but I am open to other ideas.

As for sizing, it should be a standard size so that clients can print it out if they like.

Industry/Entity Type

Landscape

Requirements
Must have
• my logo
fonts: DejaVu and LainieDaySH
Easy to email
Easy to display on one page upon opening
Standard size so that printing from a home computer is easy to do.

```html
<!DOCTYPE html>
<html lang="en">
<head>
<meta charset="utf-8">
<title>Marrowfield Studio – Photography Collections</title>
<link href="https://fonts.googleapis.com/css2?family=Allura&family=Noto+Sans:wght@400&display=swap" rel="stylesheet">
<style>
  :root {
    --paper: #ffffff;
    --panel: #232222;
    --card: #2f2d2c;
    --band: #707070;
    --ink-light: #e6e6e6;
    --ink-faint: #5a5a5a;
    --ink-dark: #2a2a2a;
    --sans: "Noto Sans", "DejaVu Sans", sans-serif;
    --script: "Allura", cursive;
  }
  * { margin: 0; padding: 0; box-sizing: border-box; }
  html, body { width: 775px; height: 1200px; overflow: hidden; background: var(--paper); }
  body { position: relative; font-family: var(--sans); color: var(--ink-light); }

  .page { position: absolute; left: 17px; width: 741px; background: var(--panel); overflow: hidden; }
  .cover { top: 17px; height: 572px; }
  .pricing { top: 611px; height: 570px; }

  .cover-band { position: absolute; background: var(--band); }
  .cover-band--top { right: 0; top: 0; width: 371px; height: 65px; }
  .cover-band--bottom { left: 0; bottom: 0; width: 370px; height: 64px; }

  .brand-disc { position: absolute; left: 185px; top: 90px; width: 370px; height: 370px; border-radius: 50%; background: var(--paper); }
  .brand-name { position: absolute; left: 185px; top: 255px; width: 370px; text-align: center; font-family: var(--sans); font-size: 27px; letter-spacing: 2px; color: var(--ink-dark); }

  .cover-year { position: absolute; right: 96px; top: 440px; font-family: var(--script); font-size: 44px; color: var(--ink-light); }
  .cover-title { position: absolute; right: 48px; top: 494px; font-family: var(--script); font-size: 38px; color: var(--ink-light); }

  .collection { position: absolute; left: 30px; width: 310px; height: 92px; background: var(--card); border-radius: 8px; text-align: center; }
  .collection-ribbon { position: absolute; left: 0; top: 0; overflow: visible; }
  .collection-title { font-family: var(--script); font-size: 27px; line-height: 26px; margin-top: 4px; color: var(--ink-light); }
  .collection-text { font-size: 8.6px; line-height: 11px; color: var(--ink-light); padding: 0 6px; }

  .includes { position: absolute; left: 30px; top: 450px; width: 310px; text-align: center; }
  .includes-title { font-family: var(--script); font-size: 24px; line-height: 24px; }
  .includes-text { font-size: 7.4px; line-height: 8.6px; margin-top: 2px; }

  .carte { position: absolute; left: 405px; width: 320px; text-align: center; }
  .carte-title { font-family: var(--script); font-size: 24px; line-height: 24px; }
  .carte-text { font-size: 9.2px; line-height: 10.6px; margin-top: 2px; }
  .price { color: var(--ink-faint); }
</style>
</head>
<body>

<section class="page cover">
  <div class="cover-band cover-band--top"></div>
  <div class="cover-band cover-band--bottom"></div>
  <div class="brand-disc"></div>
  <div class="brand-name">MARROWFIELD STUDIO</div>
  <div class="cover-year">2013</div>
  <div class="cover-title">photography collections</div>
</section>

<section class="page pricing">
  <svg width="0" height="0" style="position:absolute">
    <defs>
      <linearGradient id="ribbon-shade" x1="0" y1="0" x2="1" y2="0">
        <stop offset="0" stop-color="#d8d8d8"/>
        <stop offset="0.6" stop-color="#a9a9a9"/>
        <stop offset="1" stop-color="#4a4a4a"/>
      </linearGradient>
    </defs>
  </svg>

  <article class="collection" style="top:34px">
    <svg class="collection-ribbon" width="110" height="50"><polygon points="0,22 100,-3 92,12 0,40" fill="url(#ribbon-shade)"/><text x="20" y="31" transform="rotate(-18 20 31)" font-family="Noto Sans, sans-serif" font-size="11" fill="#222">300 €</text></svg>
    <h2 class="collection-title">Collection 1</h2>
    <p class="collection-text">Your favorite five images from the session will be<br>professionally edited and presented to you on disk as<br>high resolution jpegs</p>
  </article>

  <article class="collection" style="top:141px">
    <svg class="collection-ribbon" width="110" height="50"><polygon points="0,22 100,-3 92,12 0,40" fill="url(#ribbon-shade)"/><text x="20" y="31" transform="rotate(-18 20 31)" font-family="Noto Sans, sans-serif" font-size="11" fill="#222">400 €</text></svg>
    <h2 class="collection-title">Collection 2</h2>
    <p class="collection-text">Your favorite ten images from the session will be<br>professionally edited and given to you on disk as<br>high resolution jpegs.<br>Your favorite image from the session will be<br>professionally printed for you (20x30cm) on Larchmere paper,<br>Maren's favorite for portraits.</p>
  </article>

  <article class="collection" style="top:247px">
    <svg class="collection-ribbon" width="110" height="50"><polygon points="0,22 100,-3 92,12 0,40" fill="url(#ribbon-shade)"/><text x="20" y="31" transform="rotate(-18 20 31)" font-family="Noto Sans, sans-serif" font-size="11" fill="#222">500 €</text></svg>
    <h2 class="collection-title">Collection 3</h2>
    <p class="collection-text">Your favorite <u>fifteen</u> images from the session will be<br>professionally edited and presented to you on disk as<br>high resolution jpegs.<br>Your favorite <u>two</u> images from the session will be<br>professionally printed for you (20x30cm) on Larchmere paper,<br>Maren's favorite for portraits.</p>
  </article>

  <article class="collection" style="top:354px">
    <svg class="collection-ribbon" width="110" height="50"><polygon points="0,22 100,-3 92,12 0,40" fill="url(#ribbon-shade)"/><text x="20" y="31" transform="rotate(-18 20 31)" font-family="Noto Sans, sans-serif" font-size="11" fill="#222">600 €</text></svg>
    <h2 class="collection-title">Collection 4</h2>
    <p class="collection-text"><u>ALL</u> presented images from the session will be<br>professionally edited and presented to you on disk as<br>high resolution jpegs (approximately 40+ images).<br>Your favorite <u>two</u> images from the session will be<br>professionally printed for you (20x30cm) on Larchmere paper,<br>Maren's favorite for portraits.</p>
  </article>

  <div class="includes">
    <h3 class="includes-title">all collections include:</h3>
    <p class="includes-text">One to two hour portrait session with photographer in location<br>of your choice (unlimited time if necessary!)<br>Maren will create a presentation video with hand-selected<br>music and custom editing, which tells your story,<br>highlights the best images, and reveals the connections within<br>your family.<br>An online gallery for viewing and ordering<br>helps you share your images with family and friends.</p>
  </div>

  <div class="carte" style="top:24px">
    <h3 class="carte-title">a la carte pricing</h3>
    <p class="carte-text">These products may be purchased separately to complement<br>your collection. A consultation with Maren will help you decide<br>which products are best for gifts and for your home.</p>
  </div>

  <div class="carte" style="top:106px">
    <h3 class="carte-title">high resolution digital images</h3>
    <p class="carte-text">Perfect if you just need to add "one more image" to your<br>collection!<br>High-resolution jpeg file <span class="price">25 €</span> each</p>
  </div>

  <div class="carte" style="top:176px">
    <h3 class="carte-title">matt prints</h3>
    <p class="carte-text">20x30 cm and smaller <span class="price">35 €</span><br>Each print is professionally edited, printed on archival photo<br>paper.<br>Purchase includes the JPEG file for your personal digital use.</p>
  </div>

  <div class="carte" style="top:252px">
    <h3 class="carte-title">larchmere prints</h3>
    <p class="carte-text">Prints on Larchmere (watercolor) paper are Maren's favorite for<br>large format color prints<br>30x40 cm <span class="price">75 €</span></p>
  </div>

  <div class="carte" style="top:325px">
    <h3 class="carte-title">canvas prints</h3>
    <p class="carte-text">Ready-to-hang, stretched canvas wall art of your favorite images<br>30x40 cm <span class="price">95 €</span></p>
  </div>

  <div class="carte" style="top:383px">
    <h3 class="carte-title">framed + matted prints</h3>
    <p class="carte-text">Beautiful Larchmere prints finished with wide mats and simple,<br>elegant frames of your choice<br>30x40 inch <span class="price">150 €</span></p>
  </div>

  <div class="carte" style="top:452px">
    <h3 class="carte-title">custom designed albums</h3>
    <p class="carte-text">Images from your session are selected for the custom design of<br>an album and bound in a book for a modern presentation of your<br>images. There are a number of cover choices for the classic<br>flush-mount and beautifully crafted albums. A great way to<br>display all of your favorite images from your session on your<br>coffee table.<br>Prices begin at <span class="price">400 €</span></p>
  </div>
</section>

</body>
</html>
```